Norvane Freight and Provision Service Brochure

Please see http://www.norvanefreight.example for who we are and what we do.
We would like to see a design that matches the industry we work in i.e. Oil and Gas. The design should communicate large, heavy field operations, supply of vast bulk fuel quantities to our US and Afghan Military customers, plus financial independence and the companies whatever it takes attitude operation in remote often hostile areas. Dark colors like on the website - contrasting our green logo. A strong focus on our past performance/past experience.

Target Market(s)

Military Customers, Partners, Subcontractors

Industry/Entity Type

Industry

Contact Information for Business Card

Display of Address, Phone, email etc. of our 4 offices

Font styles to use
Sans Serif

Requirements
Must have
• Glossy brochure, modern, cool design. Great display (map) of our offices in the Middle East, Europe and Central Asia. A focus on our past performance/past experience. Customer logos/references
Nice to have
• Prominent highlighted watermark logo
Should not have
• Standard A4/Letter brochure

```html
<!DOCTYPE html>
<html lang="en">
<head>
<meta charset="utf-8">
<title>Norvane Freight and Provision – Brochure Spread</title>
<link href="https://fonts.googleapis.com/css2?family=Saira:wght@700&family=Barlow:wght@400;500;600&family=Arimo&display=swap" rel="stylesheet">
<style>
  :root{
    --navy:#0f1f5c;
    --green:#8cf000;
    --green-line:#3ddc1f;
    --ink:#333a44;
    --heading:#1b2a6b;
    --paper:#ffffff;
    --frame:#b9b9b9;
    --badge-bg:#eef0f2;
    --badge-shape:#c9d0d8;
  }
  html,body{margin:0;padding:0;width:1200px;height:1000px;overflow:hidden;background:var(--paper);}
  body{position:relative;font-family:"Barlow",Arial,sans-serif;color:var(--ink);}
  .page{position:absolute;top:288px;height:424px;width:600px;overflow:hidden;}
  .page--left{left:0;border:1px solid var(--frame);box-sizing:border-box;background:var(--paper);}
  .page--right{left:600px;border-top:1px solid var(--green-line);box-sizing:border-box;}
  .section-band{position:absolute;top:122px;height:57px;}
  .section-band--navy{left:0;width:600px;background:var(--navy);}
  .section-band--green{left:0;width:260px;background:var(--green);}
  .section-title{position:absolute;left:40px;top:14px;margin:0;font-family:"Saira",Arial,sans-serif;font-weight:700;font-size:14px;letter-spacing:.3px;color:#fff;line-height:1;}
  .section-sub{position:absolute;left:40px;top:31px;margin:0;font-size:10px;letter-spacing:.6px;color:#fff;line-height:1;}
  .section-band--green .section-sub{color:#f2ffe0;}
  .photo{position:absolute;}
  .col-heading{position:absolute;margin:0;font-weight:600;font-size:9.5px;color:var(--heading);line-height:11px;}
  .copy{position:absolute;margin:0;font-size:7.2px;line-height:9.6px;letter-spacing:.15px;color:var(--ink);}
  .copy p{margin:0 0 5px;}
  .folio{position:absolute;top:395px;width:20px;height:28px;background:var(--green);color:#fff;font-size:5px;text-align:center;line-height:28px;}
  .badge-box{position:absolute;left:310px;top:199px;width:122px;height:93px;background:var(--badge-bg);}
  .caption{position:absolute;top:770px;font-family:"Arimo",Arial,sans-serif;font-size:24px;color:#111;}
  .overlay-panel{position:absolute;left:260px;top:122px;width:340px;height:302px;background:rgba(231,241,245,.92);}
</style>
</head>
<body>

<section class="page page--left">
  <div class="section-band section-band--navy">
    <h2 class="section-title">WHO WE ARE</h2>
    <p class="section-sub">PAST PERFORMANCE &amp; QA_QC STANDARDS</p>
  </div>

  <div class="photo" role="img" aria-label="Rating checklist with pen marking Exceptional" style="left:40px;top:199px;width:125px;height:84px;background:linear-gradient(135deg,#f4f4f4,#d9dde2);"></div>

  <h3 class="col-heading" style="left:172px;top:200px;">Proven Track Record</h3>
  <div class="copy" style="left:172px;top:214px;width:120px;">
    <p>Our proven performance track record of delivering procurement, transportation, storage, technology and distribution services to clients working in Afghanistan and Central Asia is unmatched.</p>
  </div>
  <div class="copy" style="left:40px;top:287px;width:252px;">
    <p>Our proven history of delivering the highest quality of products and services rapidly and securely in all conditions sets is second to None in our industry.</p>
    <p>The trust and confidence based on our strength of performance given to us by our customers has been and is reflected in being awarded with many Prime-Vendor Contracts by the Government of the United States of America, the Government of the Islamic Republic of Afghanistan.</p>
  </div>

  <div class="badge-box" role="img" aria-label="Quality certification badge">
    <svg width="122" height="93" viewBox="0 0 122 93" aria-hidden="true">
      <circle cx="61" cy="46" r="38" fill="var(--badge-shape)"/>
    </svg>
  </div>

  <h3 class="col-heading" style="left:441px;top:200px;">Commitment to Quality</h3>
  <div class="copy" style="left:441px;top:214px;width:118px;">
    <p>Norvane Freight and Provision Service is committed in all of its operations to the principles of quality, safety, environment, health and legal compliance. We have integrated ISO 9001 and ISO 14001 based standards into our work control management systems system.</p>
  </div>
  <div class="copy" style="left:310px;top:302px;width:254px;">
    <p>These standards have become binding regulations in the entire group of companies for the fields of quality, safety, environment and health (HSEQ).</p>
    <p>Augmenting our internal corporate team, Norvane incorporates international management methodologies to affect a systemic corporate culture of quality improvement and working closely with our personnel to insert time-tested and proven best practices into our corporate and operational structures.</p>
  </div>

  <div class="folio" style="left:539px;">12</div>
</section>

<section class="page page--right">
  <div class="photo" role="img" aria-label="Team hands working over a world map table" style="left:0;top:0;width:600px;height:424px;background:linear-gradient(160deg,#14344a 0%,#1f5a6e 45%,#38b7c6 70%,#123042 100%);"></div>
  <div class="overlay-panel"></div>
  <div class="section-band section-band--green">
    <h2 class="section-title">WHO WE ARE</h2>
    <p class="section-sub">OUR VALUE</p>
  </div>

  <div class="photo" role="img" aria-label="Cupped hands holding soil with a green seedling" style="left:284px;top:180px;width:142px;height:99px;background:linear-gradient(135deg,#e9c7a8,#7a5234 55%,#3e2a1a);"></div>

  <h3 class="col-heading" style="left:436px;top:180px;width:124px;">What We Stand For. How We Think And Act.</h3>
  <div class="copy" style="left:436px;top:206px;width:124px;">
    <p>Norvane Freight and Provision Service is characterised by a strong corporate culture. Four core values form the pillars, which support the structure of Norvane beyond the borders of the regions we operate in, connect people within the company and at the</p>
  </div>
  <div class="copy" style="left:284px;top:283px;width:278px;">
    <p>same time represent the mission statement for daily work: Independence, Sustainability, Commitment and Service Excellence. We are committed to fair competition and social responsibility towards both the population and the environment: the company denounces discrimination and child labour, advocates human rights and takes measures for employment, occupational and environmental protection. These and the other guidelines of the Norvane code of conduct are implemented to ensure that our value system is adapted to the largest possible extent throughout our worldwide locations. In order to achieve this, we focus on the ability, the strength and the commitment of all people in our organization.</p>
  </div>

  <div class="folio" style="left:540px;">13</div>
</section>

<div class="caption" style="left:313px;">Page 12</div>
<div class="caption" style="left:845px;">Inside Back</div>

</body>
</html>
```